Summit Ridge Business Card

Side 1: Summit Ridge Logo (logo without Maltese cross) with industrial rope rescue related theme. Our company services - TRAINING - Fire Training, Confined Space Rescue Training, Rope Rescue training, Hazmat Training, Incident Command, EMS, Pump Operations Training. Website - summitridgeexample.com.
Side 2: Summit Ridge Fire Department Logo (logo with Maltese cross) with Firefighter related theme. Company (division) services - FIELD SERVICES - Fire Department, Stand-by Rescue, Safety, EMS, Planning. "Supporting the Emergency Response Community Since 1967"

Add contact information wherever it makes since (Name, Email, Phone).
I would like it to represent the Summit Ridge Fire Department Logo as a division not as a separate entity without saying it, possibly by depicting it in the background of Side 2 instead of being a standalone picture like the logo on Side 1.

```html
<!DOCTYPE html>
<html lang="en">
<head>
<meta charset="utf-8">
<title>Summit Ridge Business Card</title>
<link rel="stylesheet" href="https://fonts.googleapis.com/css2?family=Poppins:wght@400;500;600;700&display=swap">
<style>
  :root {
    --red: #ff0000;
    --tag-red: #ff3b1f;
    --black: #000000;
    --white: #ffffff;
    --ink: #111111;
    --stage: #1e1e1e;
  }
  * { box-sizing: border-box; margin: 0; padding: 0; }
  html, body { width: 1200px; height: 1015px; overflow: hidden; }
  body {
    background: var(--stage);
    font-family: "Poppins", sans-serif;
    display: flex;
    flex-direction: column;
    align-items: center;
    justify-content: center;
    gap: 40px;
  }
  .card {
    position: relative;
    width: 760px;
    height: 434px;
    background: var(--white);
    overflow: hidden;
  }
  .band {
    position: absolute;
    left: 0; right: 0;
    background: var(--red);
    color: var(--white);
    text-align: center;
    font-weight: 600;
    text-transform: uppercase;
  }
  .strip {
    position: absolute;
    left: 0; right: 0; bottom: 0;
    background: var(--black);
    text-align: center;
  }
  /* Front */
  .front .brand {
    position: absolute;
    top: 92px; left: 0; right: 0;
    text-align: center;
  }
  .brand-name {
    display: inline-flex;
    align-items: center;
    gap: 14px;
    font-weight: 700;
    font-size: 46px;
    letter-spacing: 3px;
    color: var(--red);
    text-transform: uppercase;
  }
  .brand-dot {
    width: 22px; height: 22px;
    border-radius: 50%;
    background: var(--red);
  }
  .front .band {
    top: 228px; height: 140px;
    padding-top: 20px;
    font-size: 17px;
    line-height: 33px;
    letter-spacing: 0.5px;
  }
  .front .strip {
    height: 66px;
    line-height: 66px;
    font-size: 20px;
    letter-spacing: 1.5px;
    color: var(--white);
  }
  .front .strip .domain { color: var(--red); }
  /* Back */
  .back .contact {
    position: absolute;
    left: 54px; top: 92px;
    color: var(--ink);
  }
  .contact-name { font-weight: 700; font-size: 30px; letter-spacing: 0.5px; }
  .contact-line {
    display: flex; align-items: center; gap: 10px;
    font-size: 19px; line-height: 30px; letter-spacing: 0.5px;
  }
  .contact-line svg { width: 18px; height: 18px; flex: none; }
  .division {
    position: absolute;
    right: 42px; top: 56px;
    width: 230px;
    text-align: center;
    font-weight: 700;
    font-size: 26px;
    line-height: 32px;
    letter-spacing: 1px;
    color: var(--tag-red);
    text-transform: uppercase;
  }
  .back .band {
    top: 240px; height: 120px;
    padding-top: 18px;
    font-size: 27px;
    line-height: 40px;
    letter-spacing: 1px;
  }
  .back .strip {
    height: 74px;
    line-height: 74px;
    font-size: 19px;
    font-weight: 500;
    color: var(--tag-red);
    letter-spacing: 0.5px;
  }
</style>
</head>
<body>
  <section class="card front">
    <div class="brand">
      <span class="brand-name"><span class="brand-dot"></span>Summit Ridge</span>
    </div>
    <div class="band services">
      Fire Training • Confined Space Rescue Training<br>
      Rope Rescue Training • Hazmat Training<br>
      Incident Command • EMS • Pump Operations Training
    </div>
    <div class="strip website">www.<span class="domain">summitridgeexample</span>.com</div>
  </section>

  <section class="card back">
    <div class="contact">
      <p class="contact-name">Daniel Hayes</p>
      <p class="contact-line">
        <svg viewBox="0 0 24 24" aria-hidden="true"><path fill="#ff3b1f" d="M6.6 10.8a15.1 15.1 0 0 0 6.6 6.6l2.2-2.2a1 1 0 0 1 1-.25 11.4 11.4 0 0 0 3.6.57 1 1 0 0 1 1 1V20a1 1 0 0 1-1 1A17 17 0 0 1 3 4a1 1 0 0 1 1-1h3.5a1 1 0 0 1 1 1c0 1.25.2 2.45.57 3.6a1 1 0 0 1-.25 1z"/></svg>
        044-555 010 234
      </p>
      <p class="contact-line">
        <svg viewBox="0 0 24 24" aria-hidden="true"><path fill="#ff3b1f" d="M2 5h20v14H2z"/><path fill="none" stroke="#fff" stroke-width="1.6" d="M2.5 5.5 12 13l9.5-7.5"/></svg>
        contact@summitridgeexample.com
      </p>
    </div>
    <div class="division">Summit Ridge Fire Department</div>
    <div class="band field-services">
      Fire Department • Stand-by Rescue<br>
      Safety • EMS • Planning
    </div>
    <div class="strip tagline">Supporting the Emergency Response Community Since 1967</div>
  </section>
</body>
</html>
```